Super elegant, crisp & clean Business card design required

We recently upgraded our branding - which is on our website - talvendoraphoto.com

I would like a simple, yet elegant, clean business card design please.

The font of my logo is Cinzel - and because of the natural colour - it's best to have this on a black background.

I would like to have the back of the business card - with simply my logo.

PLEASE DO NOT SUBMIT A COMPLICATED / UNCLEAN DESIGN

Industry/Entity Type

Business

Contact Information for Business Card

Talven Doroshko Photography

Font styles to use
Other font styles liked:
• Cinzel

Requirements
Must have
• A backpage with nothing but my logo
• Simple design - stands out
Should not have
• Colour that dont align with my logo
• Over complicated '/ non symmetrical design

```html
<!DOCTYPE html>
<html lang="en">
<head>
<meta charset="utf-8">
<title>Talven Doroshko Photography – Business Card</title>
<link rel="stylesheet" href="https://fonts.googleapis.com/css2?family=Cinzel:wght@400&family=Arimo:wght@400&display=swap">
<style>
  :root {
    --page-bg: #e9e6e1;
    --card-top: #f4f3f1;
    --card-bottom: #dcdad6;
    --card-edge: #c9c6c1;
    --panel-black: #0b0a09;
    --panel-sheen: #1c1a18;
    --logo-taupe: #7b6f61;
    --gold-brown: #7a6241;
  }
  * { margin: 0; padding: 0; box-sizing: border-box; }
  html, body {
    width: 1200px; height: 970px; overflow: hidden;
    background: var(--page-bg);
  }
  .card {
    position: absolute; left: 120px; top: 212px;
    width: 960px; height: 545px;
    background: linear-gradient(180deg, var(--card-top), var(--card-bottom));
    border: 1px solid var(--card-edge);
    box-shadow: 0 10px 30px rgba(0,0,0,0.12);
  }
  .edge-tab {
    position: absolute; left: 0; top: 113px;
    width: 32px; height: 319px;
    background: var(--panel-black);
    border-radius: 0 18px 18px 0;
  }
  .brand {
    position: absolute; left: 49px; top: 150px; width: 400px;
    text-align: center; color: var(--logo-taupe);
    font-family: "Cinzel", serif; font-weight: 400;
  }
  .brand-mark {
    display: block; margin: 0 auto 34px;
    width: 110px; height: 110px;
  }
  .brand-name { font-size: 29px; letter-spacing: 0.02em; line-height: 1; }
  .brand-line { font-size: 15px; letter-spacing: 0.42em; margin-top: 10px; padding-left: 0.42em; }
  .info-panel {
    position: absolute; right: 0; top: 113px;
    width: 487px; height: 319px;
    background: linear-gradient(160deg, var(--panel-sheen), var(--panel-black) 55%);
    border-radius: 18px 0 0 18px;
    color: var(--gold-brown);
  }
  .person-name {
    position: absolute; left: 38px; top: 34px;
    font-family: "Cinzel", serif; font-size: 35px; letter-spacing: 0.03em;
  }
  .person-title {
    position: absolute; left: 38px; top: 78px;
    font-family: "Arimo", sans-serif; font-size: 22px;
  }
  .contact-list {
    position: absolute; left: 38px; top: 190px; list-style: none;
    font-family: "Arimo", sans-serif; font-size: 23px;
  }
  .contact-list li { display: flex; align-items: center; height: 34px; }
  .contact-list svg { width: 20px; height: 20px; margin-right: 14px; flex: none; }
</style>
</head>
<body>
  <div class="card">
    <div class="edge-tab"></div>

    <div class="brand">
      <svg class="brand-mark" viewBox="0 0 110 110" aria-hidden="true">
        <circle cx="55" cy="55" r="52" fill="none" stroke="var(--logo-taupe)" stroke-width="2"/>
      </svg>
      <div class="brand-name">Talven Doroshko</div>
      <div class="brand-line">PHOTOGRAPHY</div>
    </div>

    <div class="info-panel">
      <div class="person-name">ORRIN VALE</div>
      <div class="person-title">Chief Executive Officer</div>
      <ul class="contact-list">
        <li>
          <svg viewBox="0 0 24 24" aria-hidden="true"><path d="M6.6 2.5l3 3.4-1.8 2.4c1.3 2.9 3.4 5 6.2 6.3l2.4-1.8 3.4 3-1.7 3.4C12 19 5 12 3.3 4.2z" fill="none" stroke="var(--gold-brown)" stroke-width="1.8" stroke-linejoin="round"/></svg>
          44 7700 900412
        </li>
        <li>
          <svg viewBox="0 0 24 24" aria-hidden="true"><rect x="2" y="5" width="20" height="14" fill="none" stroke="var(--gold-brown)" stroke-width="1.8"/><path d="M2 5l10 8 10-8" fill="none" stroke="var(--gold-brown)" stroke-width="1.8"/></svg>
          td.photography@fernpost.com
        </li>
        <li>
          <svg viewBox="0 0 24 24" aria-hidden="true"><g fill="none" stroke="var(--gold-brown)" stroke-width="1.6"><circle cx="12" cy="12" r="9.5"/><ellipse cx="12" cy="12" rx="4.2" ry="9.5"/><path d="M2.5 12h19M4 7h16M4 17h16"/></g></svg>
          www.talvendoraphoto.com
        </li>
      </ul>
    </div>
  </div>
</body>
</html>
```